Business Card Design Project

I have a two letter domain name zu.com.au (lower case font please). I want a business card, cum logo that is die cut (around the zu segment at least) that fits standard business card size.
zu is all about what 'I am' - a journalist, blogger, analyst, commentator. My mantra is "I think therefore zu'.
The reverse of the card only needs my name Olin Verka, email olin@zu.com.au and mobile +61 437 185 923
Mainly people that will use my professional writing services and suppliers that will provide product for review
Business
- One side is zu.com.au (hint - the .com.au can be vertical or horizontal to fit - the zu should be as large as possible).
The other requires large size font name, email and phone details (so no one needs glasses to read it).
The die cut can be just to highlight the zu segment - need not be around the whole card.
Font used in the past was Belwe (old style - very much like the i used in the information symbol).
Colours - no preference - prefer two colour to process colour but can also be an outline font instead of solid colour.

```html
<!DOCTYPE html>
<html lang="en">
<head>
<meta charset="utf-8">
<title>zu.com.au business card</title>
<link href="https://fonts.googleapis.com/css2?family=Arvo:wght@400;700&display=swap" rel="stylesheet">
<style>
  :root {
    --backdrop: #e9e2d8;
    --card: #3a3a3b;
    --card-edge: #2c2c2d;
    --yellow: #fff200;
    --deboss: #262627;
    --text-font: "Arvo", serif;
  }
  html, body {
    margin: 0;
    width: 1200px;
    height: 960px;
    overflow: hidden;
    background: var(--backdrop);
  }
  .canvas {
    position: relative;
    width: 1200px;
    height: 960px;
  }
  .card {
    position: absolute;
    left: 260px;
    width: 680px;
    height: 378px;
    background: var(--card);
    border-radius: 20px;
    box-shadow: 0 6px 0 var(--card-edge), 0 18px 40px rgba(0,0,0,0.25);
    font-family: var(--text-font);
    color: var(--yellow);
    overflow: hidden;
  }
  .card-front { top: 70px; }
  .card-back { top: 500px; }

  .brand-name {
    position: absolute;
    left: 0;
    right: 0;
    top: 50%;
    transform: translateY(-50%);
    margin: 0;
    text-align: center;
    font-weight: 700;
    font-size: 76px;
    line-height: 1;
    color: var(--yellow);
  }

  .contact {
    position: absolute;
    left: 64px;
    top: 62px;
  }
  .contact-name {
    font-weight: 700;
    font-size: 38px;
    letter-spacing: 1.5px;
    margin: 0 0 18px;
  }
  .contact-line {
    display: flex;
    align-items: center;
    gap: 20px;
    font-size: 33px;
    letter-spacing: 1.5px;
    margin: 0 0 10px;
  }
  .contact-icon {
    width: 22px;
    height: 22px;
    flex: none;
  }
  .back-domain {
    position: absolute;
    left: 64px;
    bottom: 48px;
    margin: 0;
    font-weight: 700;
    font-size: 22px;
    color: var(--deboss);
  }
</style>
</head>
<body>
<main class="canvas">
  <section class="card card-front" aria-label="Card front">
    <p class="brand-name">zu.com.au</p>
  </section>

  <section class="card card-back" aria-label="Card back">
    <div class="contact">
      <p class="contact-name">Olin Verka</p>
      <p class="contact-line">
        <svg class="contact-icon" viewBox="0 0 22 22" aria-hidden="true">
          <rect x="2" y="5" width="18" height="12" fill="none" stroke="#fff200" stroke-width="2"/>
          <path d="M2 5 L11 12 L20 5" fill="none" stroke="#fff200" stroke-width="2"/>
        </svg>
        <span>olin@zu.com.au</span>
      </p>
      <p class="contact-line">
        <svg class="contact-icon" viewBox="0 0 22 22" aria-hidden="true">
          <rect x="5" y="2" width="12" height="18" rx="2" fill="none" stroke="#fff200" stroke-width="2"/>
          <line x1="9" y1="17" x2="13" y2="17" stroke="#fff200" stroke-width="2"/>
        </svg>
        <span>+61 437 185 923</span>
      </p>
    </div>
    <p class="back-domain">zu.com.au</p>
  </section>
</main>
</body>
</html>
```